Banner ad design for Vorlix Display Ads

We are looking for a designer to develop a concept for banner ads for a Vorlix Display campaign we are building.

We have 3 business lines, shredding services, records management services and scanning services.

We are looking for 4 sets of ads to be created, one for each business line + one set that showcases all of our lines together.

For the design concepts, we would like to see a few sizes (banner, square, leaderboard, skyscraper, etc) for each.

The person chosen will then need to create the ads into all Vorlix supported sizes -- 20 sizes total for each set of ads as per the Vorlix size guidelines found on this page - https://help.vorlix.com/vorlix-ads/answer/5830417?hl=en&ref_topic=6402871#

A few items to note:
- Design should complement our existing brand/website look and feel (www.tamrock-dunes.ca)
- Each final ad must be 150Kb or less in size
- Final designs should be editable, meaning if we would like to change some copy in the design, we can do so using a well-known software (Canva, Photoshop/InDesign, etc)
- Some images are attached for use, but if you feel a different stock image is more suitable to to your design, please go ahead and use it.

Provided below is some messaging that can be used for each set of ads. Do not feel you need to use all of the messaging, it is provided for guidance.

SHREDDING SERVICES:

Possible Short Headline:
-- One-Time Shredding Services
-- Secure Shredding Services
-- Affordable On-Site Shredding

Possible Long Headline
-- Your Paper Can be Destroyed as Soon as the Next Business Day

Possible Descriptions:
-- TORV QQQ Certified On site shredding company. Service as soon as Next Day.
-- Secure and Affordable Toronto & GTA On-Site Shredding.
-- Certified, Affordable Office Shredding Since 2003.
-- Quick, no contact and affordable paper shredding services in Toronto & Southern Ontario.
-- Certified, Affordable Office Shredding Since 2003. Fast, no contact shredding service.

Call to Action
-- Get a Quote

RECORDS MANAGEMENT
Short Headline:
-- Off-site Records Storage
-- Records Management & Storage
-- Secure Records Storage
-- Records Management Services
-- Long Term Records Management
-- Document Storage Solutions

Possible Description
-- Local, Affordable Storage Solutions. Protect and Store your Documents in our Secure Facility
-- Local, Affordable Records Management Solutions. Store your Records in our Secure Facility
-- Certified, Affordable Document Storage Since 2004. Contact Us for a Free Quote!
-- Veltra+ Certified, Affordable Document Storage Since 2004. Contact Us for a Free Quote!

Call to Action
-- Get a Quote

SCANNING SERVICES

Short Headline:
-- Professional Scanning Company
-- Toronto & GTA Scanning Service
-- Document Scanning Services
-- Digital Conversion Services
-- Fast & Easy Retrieval

Description
-- Scan and documents and files with Professional scanning services from Tamrock-Dunes
-- Convert Your Paper Files to Electronic Files. Fast & Easy Retrieval.
-- Easily access your documents electronically with Document Scanning Services

Call to Action
-- Get a Quote

ALL SERVICES AD SET
Short Headline
-- Shred, Scan & Store Documents
-- Secure Shredding, Records Management and Scanning Services
-- #1 Document Management Company
-- Tamrock Dunes Shredding, Storage & Scanning

Description
-- Secure and Affordable Toronto & GTA On-Site Shredding, Document Storage & Scanning Company

Call to Action
-- Get a Quote

Font styles to use
Sans Serif

```html
<!DOCTYPE html>
<html lang="en">
<head>
<meta charset="utf-8">
<title>Tamrock-Dunes Display Ads</title>
<link rel="stylesheet" href="https://fonts.googleapis.com/css2?family=Montserrat:wght@800&family=Roboto:wght@400;500&family=Lato:wght@400;700&display=swap">
<style>
  :root {
    --page-grey: #7f7f7f;
    --brand-blue: #1687cf;
    --brand-blue-light: #3ea2e0;
    --ink: #121212;
    --white: #ffffff;
  }
  html, body {
    margin: 0;
    width: 1200px;
    height: 895px;
    overflow: hidden;
    background: var(--page-grey);
  }
  .stage {
    position: absolute;
    left: 0;
    top: 0;
    width: 1368px;
    height: 1020px;
    transform: scale(0.8772);
    transform-origin: 0 0;
  }
  .ad {
    position: absolute;
    width: 580px;
    height: 400px;
    background: var(--brand-blue);
    overflow: hidden;
    box-shadow: 0 2px 8px rgba(0,0,0,0.25);
    color: var(--white);
  }
  .ad--shred   { left: 79px;  top: 84px; }
  .ad--storage { left: 709px; top: 84px; }
  .ad--scan    { left: 79px;  top: 536px; }
  .ad--all     { left: 709px; top: 536px; }
  .ad__art {
    position: absolute;
    inset: 0;
    width: 580px;
    height: 400px;
  }
  .brand {
    position: absolute;
    top: 40px;
    font-family: "Lato", sans-serif;
  }
  .brand--left  { left: 28px; }
  .brand--right { right: 32px; text-align: right; }
  .brand__name {
    display: flex;
    align-items: center;
    gap: 8px;
    font-weight: 700;
    font-size: 30px;
    line-height: 1;
    color: var(--white);
  }
  .brand--right .brand__name { justify-content: flex-end; }
  .brand__mark {
    width: 12px;
    height: 12px;
    background: var(--white);
  }
  .brand__tagline {
    margin-top: 6px;
    font-size: 18px;
    letter-spacing: 0.5px;
  }
  .ad__headline {
    position: absolute;
    left: 24px;
    margin: 0;
    font-family: "Montserrat", sans-serif;
    font-weight: 800;
    font-size: 20px;
    line-height: 26px;
  }
  .ad__body {
    position: absolute;
    left: 24px;
    margin: 0;
    font-family: "Roboto", sans-serif;
    font-weight: 500;
    font-size: 17.5px;
    line-height: 26px;
  }
  .ad__fine {
    position: absolute;
    left: 24px;
    margin: 0;
    font-family: "Roboto", sans-serif;
    font-weight: 400;
    font-size: 13.5px;
    line-height: 22px;
  }
  .ad__cta {
    position: absolute;
    left: 383px;
    width: 174px;
    height: 52px;
    border-radius: 26px;
    background: var(--ink);
    color: var(--white);
    font-family: "Roboto", sans-serif;
    font-weight: 500;
    font-size: 19px;
    line-height: 52px;
    text-align: center;
  }
</style>
</head>
<body>
<div class="stage">

  <!-- Shredding -->
  <section class="ad ad--shred">
    <svg class="ad__art" viewBox="0 0 580 400">
      <defs>
        <linearGradient id="tone-shred" x1="0" y1="0" x2="1" y2="1">
          <stop offset="0" stop-color="#2a2c33"/>
          <stop offset="0.55" stop-color="#5d5a5c"/>
          <stop offset="1" stop-color="#3a3a3e"/>
        </linearGradient>
      </defs>
      <polygon role="img" aria-label="Photo: hands sorting a stack of paper documents on a desk" points="0,0 580,0 580,155 495,222 0,153" fill="url(#tone-shred)"/>
      <polygon points="0,153 150,150 300,135 495,222" fill="var(--brand-blue-light)" opacity="0.55"/>
    </svg>
    <div class="brand brand--left">
      <div class="brand__name">Tamrock-Dunes<span class="brand__mark"></span></div>
      <div class="brand__tagline">Information Security</div>
    </div>
    <h2 class="ad__headline" style="top:229px">One-Time Shredding Services</h2>
    <p class="ad__body" style="top:270px">Your Paper Can be Destroyed as Soon<br>as the Next Business Day</p>
    <p class="ad__fine" style="top:333px">TORV QQQ Certified On site shredding company.<br>Service as soon as Next Day.</p>
    <div class="ad__cta" style="top:311px">Get a Quote</div>
  </section>

  <!-- Records storage -->
  <section class="ad ad--storage">
    <svg class="ad__art" viewBox="0 0 580 400">
      <defs>
        <linearGradient id="tone-storage" x1="0" y1="0" x2="1" y2="0">
          <stop offset="0" stop-color="#4e5660"/>
          <stop offset="0.5" stop-color="#9a9488"/>
          <stop offset="1" stop-color="#3d4650"/>
        </linearGradient>
      </defs>
      <polygon role="img" aria-label="Photo: hand pulling a folder from rows of coloured file folders" points="0,0 580,0 580,176 480,245 0,176" fill="url(#tone-storage)"/>
      <polygon points="0,176 100,160 320,155 480,245" fill="var(--brand-blue-light)" opacity="0.55"/>
    </svg>
    <div class="brand brand--left">
      <div class="brand__name">Tamrock-Dunes<span class="brand__mark"></span></div>
      <div class="brand__tagline">Information Security</div>
    </div>
    <h2 class="ad__headline" style="top:247px">Off-site Records Storage</h2>
    <p class="ad__body" style="top:288px">Local, Affordable Storage Solutions.<br>Protect and Store your Documents in<br>our Secure Facility</p>
    <div class="ad__cta" style="top:311px">Get a Quote</div>
  </section>

  <!-- Scanning -->
  <section class="ad ad--scan">
    <svg class="ad__art" viewBox="0 0 580 400">
      <defs>
        <linearGradient id="tone-scan" x1="0" y1="0" x2="1" y2="0">
          <stop offset="0" stop-color="#3c3f45"/>
          <stop offset="0.5" stop-color="#b8b2a8"/>
          <stop offset="1" stop-color="#5a5a5c"/>
        </linearGradient>
      </defs>
      <polygon role="img" aria-label="Photo: staff member working at an office scanning station" points="0,0 580,0 580,178 490,245 0,176" fill="url(#tone-scan)"/>
      <polygon points="0,176 90,155 330,160 490,245" fill="var(--brand-blue-light)" opacity="0.55"/>
    </svg>
    <div class="brand brand--right">
      <div class="brand__name"><span class="brand__mark"></span>Tamrock-Dunes</div>
      <div class="brand__tagline">Information Security</div>
    </div>
    <h2 class="ad__headline" style="top:245px">Professional Scanning<br>Company</h2>
    <p class="ad__body" style="top:303px">Scan and documents and files with<br>Professional scanning services from<br>Tamrock-Dunes</p>
    <div class="ad__cta" style="top:285px">Get a Quote</div>
  </section>

  <!-- All services -->
  <section class="ad ad--all">
    <svg class="ad__art" viewBox="0 0 580 400">
      <defs>
        <linearGradient id="tone-all" x1="0" y1="0" x2="1" y2="1">
          <stop offset="0" stop-color="#3a3f5a"/>
          <stop offset="0.5" stop-color="#7a6a5c"/>
          <stop offset="1" stop-color="#4a4450"/>
        </linearGradient>
      </defs>
      <polygon role="img" aria-label="Photo: warehouse racks filled with archive boxes" points="0,0 580,0 580,178 480,245 0,176" fill="url(#tone-all)"/>
      <polygon points="0,176 120,155 330,165 480,245" fill="var(--brand-blue-light)" opacity="0.55"/>
    </svg>
    <div class="brand brand--right">
      <div class="brand__name"><span class="brand__mark"></span>Tamrock-Dunes</div>
      <div class="brand__tagline">Information Security</div>
    </div>
    <h2 class="ad__headline" style="top:245px">Shred, Scan &amp; Store<br>Documents</h2>
    <p class="ad__body" style="top:303px">Secure and Affordable Toronto &amp; GTA<br>On-Site Shredding, Document Storage<br>&amp; Scanning Company</p>
    <div class="ad__cta" style="top:285px">Get a Quote</div>
  </section>

</div>
</body>
</html>
```